Need a website setup for our new removalist business.
Our business is called Harbour Lane Removals and would like a website setup.
We don’t have a website, logo or design as of yet. Our truck is blue so something possibly that works and can incorporate the blue.

```html
<!DOCTYPE html>
<html lang="en">
<head>
<meta charset="utf-8">
<title>Harbour Lane Removals</title>
<link href="https://fonts.googleapis.com/css2?family=Oswald:wght@400;500;600&family=Lato:wght@400;700&family=Playfair+Display:wght@700&family=Poppins:wght@500&display=swap" rel="stylesheet">
<style>
:root{
  --navy:#0b2157;
  --navy-deep:#071a45;
  --blue:#2f7fe0;
  --blue-bright:#3a86ea;
  --ink:#111;
  --grey:#444;
  --pale:#f1f5fc;
  --white:#fff;
  --star:#f5b428;
}
*{box-sizing:border-box;margin:0;padding:0}
html,body{width:1200px;height:4251px;overflow:hidden}
body{position:relative;font-family:'Lato',sans-serif;color:var(--ink);background:var(--white)}
.abs{position:absolute}
.head{font-family:'Oswald',sans-serif;font-weight:600;text-transform:uppercase}
.center{text-align:center;left:0;width:1200px}
.kicker{font-family:'Lato',sans-serif;color:var(--blue);letter-spacing:4px;font-size:16px;text-transform:uppercase}

/* top bar */
.topbar{left:0;top:0;width:1200px;height:41px;background:linear-gradient(90deg,var(--navy) 0%,#1c4fae 50%,var(--navy) 100%);color:#fff;font-family:'Oswald',sans-serif;font-size:14px}
.topbar span{position:absolute;top:12px}
.nav{left:0;top:41px;width:1200px;height:86px;background:#fff;box-shadow:0 2px 6px rgba(0,0,0,.08)}
.nav a{position:absolute;top:31px;font-family:'Oswald',sans-serif;font-size:15px;color:var(--ink);text-decoration:none;text-transform:uppercase}
.nav .active{background:var(--blue);color:#fff;padding:4px 8px;top:27px}
.nav .cta{border:2px solid var(--blue);color:var(--blue);padding:7px 14px;top:24px;border-top:none}
.logo-badge{left:480px;top:-30px;width:240px;height:240px;border-radius:50%;background:rgba(255,255,255,.55);z-index:3}
.logo-badge .inner{position:absolute;left:20px;top:20px;width:200px;height:200px;border-radius:50%;background:#fff}
.logo-name{font-family:'Oswald',sans-serif;font-weight:600;color:var(--navy);text-align:center;position:absolute;left:0;width:200px}

/* hero */
.hero{left:0;top:127px;width:1200px;height:560px;background:linear-gradient(180deg,#6f93b8 0%,#4c6f90 35%,#2f5d78 65%,#1d5a6d 100%)}
.hero-title1{top:278px;font-size:38px;color:#fff}
.hero-title2{top:330px;font-size:84px;color:#fff;line-height:1}
.btn-appt{left:444px;top:472px;width:295px;height:62px;background:#fff;color:var(--blue);font-family:'Oswald',sans-serif;font-weight:500;font-size:20px;text-align:center;line-height:62px}
.band-text{top:726px;left:160px;width:880px;text-align:center;color:#fff;font-family:'Playfair Display',serif;font-size:23px;line-height:43px}

/* about */
.section-title{font-size:44px;color:var(--ink)}
.about-text{left:674px;top:1118px;width:415px;font-size:14.5px;line-height:25.8px;text-align:justify;color:#222}
.btn-line{border-top:3px solid var(--blue);border-bottom:3px solid var(--blue);color:var(--blue);font-family:'Oswald',sans-serif;font-weight:500;font-size:17px;text-align:center}
.stat{top:1700px;width:230px;text-align:center}
.stat .num{font-family:'Oswald',sans-serif;font-weight:500;font-size:44px;color:var(--blue);line-height:1}
.stat .lbl{font-family:'Oswald',sans-serif;font-weight:500;font-size:18px;margin-top:20px;text-transform:uppercase}
.stat-rule{top:1675px;width:2px;height:182px;background:linear-gradient(180deg,rgba(47,127,224,0),var(--blue),rgba(47,127,224,0))}

/* services */
.card{top:2150px;width:298px;height:298px;background:var(--navy-deep);border-radius:4px;box-shadow:0 6px 16px rgba(0,0,0,.3)}
.card .ph{position:absolute;left:6px;top:6px;width:286px;height:160px}
.card h3{position:absolute;top:184px;width:100%;text-align:center;font-family:'Oswald',sans-serif;font-weight:500;font-size:17px;color:#fff;text-transform:uppercase}
.card p{position:absolute;top:218px;left:20px;width:258px;text-align:center;font-size:12.5px;line-height:22px;color:#c9d3ea}

/* testimonials */
.avatar{border-radius:50%}
.quote{font-family:'Playfair Display',serif;color:#d6d6d6;font-size:200px;line-height:1}
.dot{width:12px;height:12px;border-radius:50%;background:#cfd8ea;top:3128px}

/* contact */
.field{background:#fff;box-shadow:0 2px 8px rgba(0,0,0,.12);font-size:13px;color:#333;padding:18px 15px}

/* footer */
.footer-head{font-family:'Oswald',sans-serif;font-weight:500;font-size:19px;color:#fff;text-transform:uppercase}
.footer-link{font-size:14.5px;color:#d3dbee}
.social{width:30px;height:30px;border-radius:50%;border:1.5px solid #fff;top:4191px}
</style>
</head>
<body>

<!-- top bar -->
<div class="abs topbar">
  <svg class="abs" style="left:110px;top:12px" width="18" height="18" viewBox="0 0 24 24"><path fill="#fff" d="M6.6 10.8a15.1 15.1 0 0 0 6.6 6.6l2.2-2.2c.3-.3.7-.4 1-.2 1.1.4 2.3.6 3.6.6.6 0 1 .4 1 1V20c0 .6-.4 1-1 1A17 17 0 0 1 3 4c0-.6.4-1 1-1h3.5c.6 0 1 .4 1 1 0 1.3.2 2.5.6 3.6.1.3 0 .7-.2 1z"/></svg>
  <span style="left:148px;top:9px;width:1px;height:22px;background:rgba(255,255,255,.5)"></span>
  <span style="left:167px">CALL:+1 555 014 2200</span>
  <svg class="abs" style="left:825px;top:13px" width="18" height="14" viewBox="0 0 24 18"><rect width="24" height="18" rx="2" fill="#fff"/><path d="M1 2l11 8 11-8" stroke="#1c4fae" stroke-width="2" fill="none"/></svg>
  <span style="left:863px;top:9px;width:1px;height:22px;background:rgba(255,255,255,.5)"></span>
  <span style="left:884px">MAIL: info@harbourlaneremovals.com</span>
</div>

<nav class="abs nav">
  <a class="active" style="left:99px">Home</a>
  <a style="left:206px">About Us</a>
  <a style="left:330px">Services</a>
  <a style="left:789px">Blog</a>
  <a style="left:883px">Reviews</a>
  <a class="cta" style="left:975px">Contact Us</a>
</nav>

<div class="abs logo-badge">
  <div class="inner">
    <div class="logo-name" style="top:60px;font-size:30px;line-height:1">HARBOUR<br>LANE</div>
    <div class="logo-name" style="top:130px;font-size:11px;letter-spacing:4px">REMOVALS</div>
  </div>
</div>

<!-- hero -->
<div class="abs hero" role="img" aria-label="Photo of a harbour city skyline with an arch bridge and waterfront"></div>
<div class="abs head center hero-title1" style="font-weight:500">Welcome To</div>
<div class="abs head center hero-title2" style="font-weight:500">Harbour Lane Removals</div>
<div class="abs btn-appt">SCHEDULE AN APPOINTMENT</div>

<svg class="abs" style="left:0;top:630px" width="1200" height="320" viewBox="0 630 1200 320">
  <path fill="var(--blue-bright)" d="M0 640 C300 625 900 655 1200 636 L1200 940 Q600 860 0 940 Z"/>
</svg>
<p class="abs band-text">Lorem ipsum dolor sit amet, consectetur adipiscing elit, sed do eiusmod tempor incididunt ut labore et dolore magna aliqua. Ut enim ad minim veniam, quis nostrud exercitation ullamco laboris nisi ut aliquip ex ea commodo consequat.</p>

<!-- about -->
<h2 class="abs head center section-title" style="top:980px;font-weight:500">About Harbour Lane</h2>
<div class="abs kicker center" style="top:1048px">Removals</div>

<svg class="abs" style="left:105px;top:1115px" width="500" height="460" viewBox="105 1115 500 460">
  <defs><linearGradient id="ring" x1="0" y1="0" x2="1" y2="1"><stop offset="0" stop-color="#3a86ea"/><stop offset="1" stop-color="#0b2157"/></linearGradient></defs>
  <circle cx="335" cy="1345" r="222" fill="none" stroke="url(#ring)" stroke-width="7"/>
</svg>
<div class="abs avatar" style="left:127px;top:1137px;width:416px;height:416px;background:linear-gradient(160deg,#e8e6e2,#c7b9a5 55%,#9c8669)" role="img" aria-label="Photo of a smiling couple carrying cardboard moving boxes"></div>
<div class="abs avatar" style="left:383px;top:1349px;width:224px;height:224px;background:#fff"></div>
<div class="abs avatar" style="left:390px;top:1356px;width:210px;height:210px;background:linear-gradient(135deg,#e7eef6,#b57a4c 60%,#5e3c24)" role="img" aria-label="Photo of boxes loaded in the back of a removal truck"></div>

<p class="abs about-text">Lorem ipsum dolor sit amet, consectetur adipiscing elit, sed do eiusmod tempor incididunt ut labore et dolore magna aliqua. Ut enim ad minim veniam, quis nostrud exercitation ullamco laboris nisi ut aliquip ex ea commodo consequat. Duis aute irure dolor in reprehenderit in voluptate velit esse cillum dolore eu fugiat nulla pariatur. Ut enim ad minim veniam, quis nostrud exercitation ullamco laboris nisi ut aliquip ex ea commodo consequat. Ut enim ad minim veniam, quis nostrud exercitation ullamco laboris nisi ut aliquip ex ea commodo consequat. Excepteur sint occaecat occaecat cupidatat non proident, sunt in culpa qui officia deserunt mollit anim id est laborumcupidatat non proident, sunt in culpa qui officia deserunt mollit anim id est laborum.</p>
<div class="abs btn-line" style="left:674px;top:1518px;width:138px;height:50px;line-height:44px">READ MORE</div>

<!-- stats -->
<div class="abs stat" style="left:110px"><div class="num">15+</div><div class="lbl">Project Completed</div></div>
<div class="abs stat-rule" style="left:353px"></div>
<div class="abs stat" style="left:367px"><div class="num">2K+</div><div class="lbl">Lorem Ipsum Dolor</div></div>
<div class="abs stat-rule" style="left:597px"></div>
<div class="abs stat" style="left:604px"><div class="num">12+</div><div class="lbl">Excepteur Sint</div></div>
<div class="abs stat-rule" style="left:843px"></div>
<div class="abs stat" style="left:844px"><div class="num">20+</div><div class="lbl">Duis Aute Irure</div></div>

<!-- services -->
<svg class="abs" style="left:0;top:1880px" width="1200" height="700" viewBox="0 1880 1200 700">
  <path fill="var(--navy)" d="M0 1882 Q600 1998 1200 1882 L1200 2575 Q600 2495 0 2575 Z"/>
</svg>
<h2 class="abs head center" style="top:2025px;font-size:44px;color:#fff;font-weight:500">What We Offer</h2>
<div class="abs kicker center" style="top:2092px;color:#4b93f0">Services</div>

<div class="abs card" style="left:110px">
  <div class="ph" style="background:linear-gradient(135deg,#dfe4ea,#a9b4c2 60%,#6d7d96)" role="img" aria-label="Photo of a smiling mover holding a box"></div>
  <h3>Lorem Ipsum Dolor</h3>
  <p>Lorem ipsum dolor sit amet, consectetur adipiscing elit, sed do eiusmod tempor incididunt ut labore et dolore magna aliqua.</p>
</div>
<div class="abs card" style="left:451px">
  <div class="ph" style="background:linear-gradient(135deg,#0d2e5c,#1f5fb8 50%,#5a6f86)" role="img" aria-label="Photo of a blue truck driving on a highway"></div>
  <h3>Lorem Ipsum Dolor</h3>
  <p>Lorem ipsum dolor sit amet, consectetur adipiscing elit, sed do eiusmod tempor incididunt ut labore et dolore magna aliqua.</p>
</div>
<div class="abs card" style="left:792px">
  <div class="ph" style="background:linear-gradient(135deg,#e9e3da,#c6a27a 55%,#8c6a48)" role="img" aria-label="Photo of a couple unpacking moving boxes"></div>
  <h3>Lorem Ipsum Dolor</h3>
  <p>Lorem ipsum dolor sit amet, consectetur adipiscing elit, sed do eiusmod tempor incididunt ut labore et dolore magna aliqua.</p>
</div>

<!-- testimonials -->
<h2 class="abs head center section-title" style="top:2617px;font-weight:500">What Our Customer Says</h2>
<div class="abs kicker center" style="top:2686px">Testimonials</div>

<div class="abs avatar" style="left:149px;top:2830px;width:66px;height:66px;background:linear-gradient(135deg,#f1d7c4,#c8906b)" role="img" aria-label="Customer portrait"></div>
<div class="abs avatar" style="left:1027px;top:2757px;width:46px;height:46px;background:linear-gradient(135deg,#e7d2c8,#7a5548)" role="img" aria-label="Customer portrait"></div>
<div class="abs avatar" style="left:392px;top:2867px;width:13px;height:13px;background:var(--navy)"></div>
<div class="abs avatar" style="left:908px;top:2831px;width:7px;height:7px;background:var(--blue)"></div>
<div class="abs avatar" style="left:533px;top:2745px;width:134px;height:134px;background:linear-gradient(160deg,#f6d7b9,#d6a07a 55%,#1f2838)" role="img" aria-label="Portrait of the featured customer"></div>

<div class="abs center" style="top:2893px;font-family:'Poppins',sans-serif;font-weight:500;font-size:21px;color:#222">Daniel Mercer</div>
<div class="abs center" style="top:2933px;font-size:12px;color:#555">United States</div>
<div class="abs center" style="top:2958px">
  <svg width="170" height="32" viewBox="0 0 170 32">
    <g fill="var(--star)">
      <path id="st" d="M16 2l4.1 8.6 9.4 1.2-6.9 6.5 1.8 9.3L16 23l-8.4 4.6 1.8-9.3-6.9-6.5 9.4-1.2z"/>
      <use href="#st" x="34"/><use href="#st" x="68"/><use href="#st" x="102"/><use href="#st" x="136"/>
    </g>
  </svg>
</div>
<div class="abs quote" style="left:132px;top:2905px">&ldquo;</div>
<div class="abs quote" style="left:960px;top:2995px">&rdquo;</div>
<p class="abs" style="left:255px;top:3008px;width:690px;text-align:center;font-size:14.5px;line-height:25px;color:#333">Lorem ipsum dolor sit amet, consectetur adipiscing elit, sed do eiusmod tempor incididunt ut labore et dolore magna aliqua. Ut enim ad minim veniam, quis nostrud exercitation ullamco laboris nisi ut aliqte irure dolor in reprehenderit in voluptate velit esse cillum dolore eu fugiat nulla pariatur.</p>
<div class="abs dot" style="left:542px"></div>
<div class="abs dot" style="left:563px"></div>
<div class="abs dot" style="left:583px"></div>
<div class="abs dot" style="left:604px;background:var(--navy)"></div>
<div class="abs dot" style="left:624px"></div>
<div class="abs dot" style="left:645px"></div>

<!-- contact -->
<div class="abs" style="left:0;top:3227px;width:1200px;height:620px;background:var(--pale)"></div>
<div class="abs" style="left:96px;top:3301px;width:435px;height:520px;background:linear-gradient(180deg,#f1e5d8 0%,#1b2c5e 40%,#15224a 100%);border-radius:140px 140px 0 0" role="img" aria-label="Photo of three smiling movers in navy caps and uniforms"></div>
<h2 class="abs head" style="left:599px;top:3303px;font-size:44px;font-weight:500">Get In Touch With Us</h2>
<div class="abs kicker" style="left:600px;top:3372px">Contact Us</div>
<div class="abs field" style="left:599px;top:3415px;width:240px;height:50px">First Name</div>
<div class="abs field" style="left:848px;top:3415px;width:240px;height:50px">Last Name</div>
<div class="abs field" style="left:599px;top:3475px;width:240px;height:50px">Email</div>
<div class="abs field" style="left:848px;top:3475px;width:240px;height:50px">Phone number</div>
<div class="abs field" style="left:599px;top:3535px;width:489px;height:108px">Message</div>
<div class="abs btn-line" style="left:599px;top:3672px;width:136px;height:53px;line-height:47px">SUBMIT</div>

<!-- footer -->
<svg class="abs" style="left:0;top:3815px" width="1200" height="436" viewBox="0 3815 1200 436">
  <path fill="var(--navy-deep)" d="M0 3840 Q600 3805 1200 3840 L1200 4251 L0 4251 Z"/>
</svg>
<div class="abs" style="left:110px;top:3918px;width:242px;height:175px;background:#fff;border-radius:4px">
  <div class="logo-name" style="left:21px;top:45px;font-size:34px;line-height:1">HARBOUR LANE</div>
  <div class="logo-name" style="left:21px;top:95px;font-size:12px;letter-spacing:4px">REMOVALS</div>
</div>

<div class="abs footer-head" style="left:450px;top:3915px">Quick Links</div>
<div class="abs footer-link" style="left:455px;top:3962px">Home</div>
<div class="abs footer-link" style="left:455px;top:3996px">About</div>
<div class="abs footer-link" style="left:455px;top:4031px">Services</div>
<div class="abs footer-link" style="left:455px;top:4066px">Testimonials</div>
<div class="abs footer-link" style="left:455px;top:4099px">Contact Us</div>

<div class="abs footer-head" style="left:662px;top:3915px">Help Links</div>
<div class="abs footer-link" style="left:664px;top:3962px">FAQ</div>
<div class="abs footer-link" style="left:664px;top:3996px">Terms of use</div>
<div class="abs footer-link" style="left:664px;top:4031px">Privacy Policy</div>
<div class="abs footer-link" style="left:664px;top:4066px">Support Links</div>
<div class="abs footer-link" style="left:664px;top:4099px">Conditions</div>

<div class="abs footer-head" style="left:895px;top:3915px">Contact Us</div>
<svg class="abs" style="left:895px;top:3965px" width="32" height="32" viewBox="0 0 32 32"><circle cx="16" cy="16" r="16" fill="var(--blue)"/><path fill="#fff" d="M16 7a6 6 0 0 0-6 6c0 4.5 6 11 6 11s6-6.5 6-11a6 6 0 0 0-6-6zm0 8.3a2.3 2.3 0 1 1 0-4.6 2.3 2.3 0 0 1 0 4.6z"/></svg>
<div class="abs footer-link" style="left:939px;top:3963px;line-height:27px">Harbour Lane Removals<br>United States</div>
<svg class="abs" style="left:895px;top:4029px" width="32" height="32" viewBox="0 0 32 32"><circle cx="16" cy="16" r="16" fill="var(--blue)"/><path fill="#fff" d="M12.4 14.6a10 10 0 0 0 4.9 4.9l1.6-1.6c.2-.2.5-.3.8-.2.8.3 1.7.4 2.6.4.4 0 .7.3.7.7v2.5c0 .4-.3.7-.7.7A12.2 12.2 0 0 1 8.2 9.7c0-.4.3-.7.7-.7h2.5c.4 0 .7.3.7.7 0 .9.1 1.8.4 2.6.1.3 0 .6-.2.8z"/></svg>
<div class="abs footer-link" style="left:939px;top:4036px">+1 555 014 2200</div>
<svg class="abs" style="left:895px;top:4081px" width="32" height="32" viewBox="0 0 32 32"><circle cx="16" cy="16" r="16" fill="var(--blue)"/><rect x="8.5" y="11" width="15" height="11" rx="1.5" fill="#fff"/><path d="M9 12l7 5 7-5" stroke="var(--blue)" stroke-width="1.5" fill="none"/></svg>
<div class="abs footer-link" style="left:939px;top:4088px">info@harbourlane.com</div>

<div class="abs" style="left:110px;top:4164px;width:980px;height:1px;background:rgba(255,255,255,.25)"></div>
<div class="abs social" style="left:110px;background:var(--blue);border-color:var(--blue)"></div>
<div class="abs social" style="left:168px"></div>
<div class="abs social" style="left:226px"></div>
<div class="abs social" style="left:284px"></div>
<div class="abs" style="left:600px;top:4198px;width:489px;text-align:right;font-size:14.5px;color:#fff">Copyrights@2024.Harbour Lane Removals.All Rights Reserved</div>

</body>
</html>
```